BUSINESS CARD - HALLORAN FIELD SERVICES

I would like to create a business card for my fertilizer spreading business. I would like to incorporate my existing logo and also a description of the services offered. The business card will be given to farmers so must be kept simple but effective. It will also be left in stores so much also be eye catching in order to stand out from other cards.

Target Market(s)

FARMERS

Requirements
Must have
• FRONT OF CARD = EXISTING LOGO + "CUSTOMISED SPREADING" below the logo

REAR Of CARD = SERVICES OFFERED AND CONTACT DETAILS

- Bulk fertilizer including Lime, Gypsum, Manure & Compost
- Granular fertilizer including Single Super, Urea, Gran-am, & Custom Blends
- Modern equipment - Autosteer & Variable Rate Capable
- Friendly & Reliable Service
- Contact Gus: 0417 552 308
Nice to have
• utilize same color scheme as existing logo

```html
<!DOCTYPE html>
<html lang="en">
<head>
<meta charset="utf-8">
<title>Halloran Field Services – Business Card</title>
<link rel="stylesheet" href="https://fonts.googleapis.com/css2?family=Arimo:wght@400;700&display=swap">
<style>
  :root {
    --charcoal: #58585a;
    --orange: #f7941d;
    --white: #ffffff;
    --text-grey: #4a4a4c;
    --backdrop: #e9e7e3;
  }
  * { box-sizing: border-box; margin: 0; padding: 0; }
  html, body {
    width: 1200px; height: 900px; overflow: hidden;
    background: var(--backdrop);
    font-family: "Arimo", Arial, sans-serif;
  }
  .sheet {
    width: 1200px; height: 900px;
    display: flex; flex-direction: column; align-items: center; justify-content: center;
    gap: 24px;
  }
  .card {
    position: relative;
    width: 700px; height: 400px;
    overflow: hidden;
    box-shadow: 0 6px 18px rgba(0,0,0,0.18);
  }

  /* Front */
  .card--front {
    background: var(--charcoal);
    display: flex; flex-direction: column; align-items: center; justify-content: center;
    color: var(--white);
  }
  .brand-mark {
    width: 150px; height: 150px; border-radius: 50%;
    border: 10px solid var(--white);
    margin-bottom: 22px;
  }
  .brand-name {
    font-weight: 700; font-size: 40px; letter-spacing: 0.5px;
    color: var(--white);
  }
  .tagline {
    margin-top: 26px;
    font-size: 22px; letter-spacing: 4px;
    color: var(--white);
  }

  /* Back */
  .card--back { background: var(--white); }
  .card-wave { position: absolute; inset: 0; width: 100%; height: 100%; }
  .wave-charcoal { fill: var(--charcoal); }
  .wave-orange { fill: var(--orange); }
  .back-mark {
    position: absolute; top: 30px; right: 55px;
    width: 150px; height: 150px; border-radius: 50%;
    background: var(--charcoal);
  }
  .services {
    position: absolute; top: 92px; left: 44px;
    list-style: none;
    color: var(--text-grey); font-size: 19px; line-height: 1.15;
  }
  .services li {
    position: relative; padding-left: 26px; margin-bottom: 4px;
  }
  .services li::before {
    content: ""; position: absolute; left: 0; top: 7px;
    width: 13px; height: 13px; border-radius: 50%;
    background: var(--orange);
  }
  .contact {
    position: absolute; right: 44px; bottom: 38px;
    text-align: right; color: var(--white);
    font-size: 30px; line-height: 1.3;
  }
  .contact-number { color: var(--orange); }
</style>
</head>
<body>
<main class="sheet">
  <section class="card card--front">
    <div class="brand-mark"></div>
    <h1 class="brand-name">HALLORAN FIELD SERVICES</h1>
    <p class="tagline">CUSTOMISED SPREADING</p>
  </section>

  <section class="card card--back">
    <svg class="card-wave" viewBox="0 0 700 400" preserveAspectRatio="none" aria-hidden="true">
      <path class="wave-orange" d="M0 332 C200 340 360 300 480 226 C380 312 210 352 0 354 Z"/>
      <path class="wave-charcoal" d="M0 364 C250 372 450 302 700 150 L700 400 L0 400 Z"/>
    </svg>
    <div class="back-mark"></div>
    <ul class="services">
      <li>Bulk fertilizer including Lime<br>Gypsum, Manure &amp; Compost</li>
      <li>Granular fertilizer including Single<br>Super, Urea, Gran-am, &amp; Custom Blends</li>
      <li>Modern equipment</li>
      <li>Autosteer &amp; Variable Rate Capable</li>
      <li>Friendly &amp; Reliable Service</li>
    </ul>
    <div class="contact">
      <p>Contact</p>
      <p>Gus: <span class="contact-number">0417 552 308</span></p>
    </div>
  </section>
</main>
</body>
</html>
```